Home Security Company Business Card

Looking for a eye catching business card that is non traditional and stands out but yet still looks professional. It should include all the pertinent information such as name, title, address, telephone, e-mail, website address should definitely stand out and then finally the logo.

Target Market(s)

Residential and Commercial accounts mostly upscale accounts

Industry/Entity Type

Security

Contact Information for Business Card

Name
Title
Address
Office #
Cell #
E-mail
Website

Font styles to use
Serif
Sans Serif

Requirements
Must have
• Logo, two sided color configuration
Nice to have
• You decide
Should not have
• There really aren't any.

```html
<!DOCTYPE html>
<html lang="en">
<head>
<meta charset="utf-8">
<title>Ironvale Security Systems – Business Card</title>
<link rel="stylesheet" href="https://fonts.googleapis.com/css2?family=Open+Sans:wght@400;600;700&display=swap">
<style>
  :root {
    --maroon: #7a1f2b;
    --maroon-dark: #5e1420;
    --gold-light: #f6e2a0;
    --gold: #e9c466;
    --gold-deep: #d49a3a;
    --paper: #ffffff;
    --backdrop: #ece7df;
  }
  html, body {
    margin: 0;
    width: 1200px;
    height: 913px;
    overflow: hidden;
    background: var(--backdrop);
    font-family: "Open Sans", Arial, sans-serif;
  }
  .canvas {
    position: relative;
    width: 1200px;
    height: 913px;
  }
  .card {
    position: absolute;
    top: 313px;
    width: 500px;
    height: 286px;
    overflow: hidden;
    box-shadow: 0 6px 18px rgba(0,0,0,0.18);
  }
  .card-front {
    left: 70px;
    background: linear-gradient(160deg, var(--gold-light) 0%, var(--gold) 55%, var(--gold-deep) 100%);
  }
  .card-back {
    left: 630px;
    background: var(--paper);
  }
  .card-shapes {
    position: absolute;
    inset: 0;
  }
  .brand {
    position: absolute;
    display: flex;
    align-items: center;
    gap: 10px;
    color: var(--maroon);
    font-weight: 600;
  }
  .brand-dot {
    flex: none;
    border-radius: 50%;
    background: var(--maroon);
  }
  .brand-name {
    line-height: 1;
    letter-spacing: 0.04em;
  }
  .brand-name .line-main { display: block; }
  .brand-name .line-sub { display: block; letter-spacing: 0.08em; margin-top: 3px; }
  .card-front .brand { left: 262px; top: 34px; }
  .card-front .brand-dot { width: 34px; height: 34px; }
  .card-front .line-main { font-size: 24px; }
  .card-front .line-sub { font-size: 9px; }
  .person {
    position: absolute;
    left: 24px;
    top: 130px;
    color: var(--maroon);
  }
  .person-name {
    margin: 0;
    font-size: 22px;
    font-weight: 700;
    line-height: 1.1;
  }
  .person-title {
    margin: 0 0 6px;
    font-size: 12px;
    text-align: right;
  }
  .person-address {
    font-style: normal;
    font-size: 13px;
    line-height: 1.4;
  }
  .contacts {
    position: absolute;
    left: 272px;
    top: 124px;
    margin: 0;
    padding: 0;
    list-style: none;
    color: var(--maroon);
    font-size: 12.5px;
    line-height: 1;
  }
  .contacts li {
    display: flex;
    align-items: center;
    gap: 8px;
    margin-bottom: 6px;
  }
  .contacts svg { width: 11px; height: 11px; flex: none; }
  .card-back .brand {
    left: 50%;
    top: 92px;
    transform: translateX(-50%);
  }
  .card-back .brand-dot { width: 52px; height: 52px; }
  .card-back .line-main { font-size: 32px; }
  .card-back .line-sub { font-size: 11px; }
  .website {
    position: absolute;
    left: 0;
    right: 0;
    top: 196px;
    margin: 0;
    text-align: center;
    color: var(--maroon);
    font-size: 15px;
    font-weight: 700;
  }
</style>
</head>
<body>
<main class="canvas">

  <section class="card card-front" aria-label="Business card front">
    <svg class="card-shapes" viewBox="0 0 500 286" aria-hidden="true">
      <line x1="0" y1="116" x2="258" y2="116" stroke="var(--maroon)" stroke-width="1"/>
      <polygon points="380,118 500,118 500,186 330,186 352,150" fill="var(--paper)"/>
      <polygon points="0,236 300,236 280,262 0,262" fill="var(--maroon)"/>
      <circle cx="312" cy="238" r="7" fill="var(--maroon-dark)"/>
    </svg>

    <div class="brand">
      <span class="brand-dot"></span>
      <span class="brand-name">
        <span class="line-main">IRONVALE</span>
        <span class="line-sub">SECURITY SYSTEMS INC.</span>
      </span>
    </div>

    <div class="person">
      <h1 class="person-name">Daniel Harwick</h1>
      <p class="person-title">Owner</p>
      <address class="person-address">248 Larkspur Avenue<br>Fairview, Ohio 44126</address>
    </div>

    <ul class="contacts">
      <li>
        <svg viewBox="0 0 12 12"><path d="M1 4c0-2 2-3 5-3s5 1 5 3l-2 1-1-2H4L3 5zM2 6h8v5H2z" fill="var(--maroon)"/></svg>
        +330 5550-0142
      </li>
      <li>
        <svg viewBox="0 0 12 12"><path d="M3 1l2 3-1 1c1 2 2 3 3 3l1-1 3 2-1 2C5 11 1 7 1 2z" fill="var(--maroon)"/></svg>
        +3305550-01783
      </li>
      <li>
        <svg viewBox="0 0 12 12"><rect x="1" y="2.5" width="10" height="7" fill="none" stroke="var(--maroon)"/><path d="M1 2.5l5 4 5-4" fill="none" stroke="var(--maroon)"/></svg>
        info@danielharwickmail.com
      </li>
    </ul>
  </section>

  <section class="card card-back" aria-label="Business card back">
    <div class="brand">
      <span class="brand-dot"></span>
      <span class="brand-name">
        <span class="line-main">IRONVALE</span>
        <span class="line-sub">SECURITY SYSTEMS INC.</span>
      </span>
    </div>
    <p class="website">www.ironvalesecuritysystemsinc.com</p>
  </section>

</main>
</body>
</html>
```